Business card design for Automotive workshop

We need a business card for a new automotive repair and tyre shop called Keelstone Prime Automotive located in New Zealand. We are a clean, modern and fresh workshop and company.

Front needs to feature logo,
my name:
Marlo Fenwicke (director)

Address:
48 Tarn Lane
Marrowby 3580

Phone: 07 594 2713
Mobile: 027 451 9362
Email: office@keelstoneautomotive.example.nz
Website: keelstoneautomotive.example.nz

Back needs to feature an area to write down appointment details, date and time.

Also feature a list of jobs and work we do such as,
Vehicle Servicing
All Mechanical Repairs
Warrant of Fitness
Tyres & Wheel Alignments
Automotive Diagnostics
Automotive Parts & Supplies

```html
<!DOCTYPE html>
<html lang="en">
<head>
<meta charset="utf-8">
<title>Keelstone Prime Automotive – Business Card</title>
<link rel="stylesheet" href="https://fonts.googleapis.com/css2?family=Montserrat:wght@400;700&display=swap">
<style>
  :root {
    --stage: #1b1b1c;
    --paper: #ffffff;
    --navy: #0b1a31;
    --red: #e3211f;
    --ink: #111111;
    --light: #f2f4f8;
  }
  * { box-sizing: border-box; margin: 0; padding: 0; }
  html, body { width: 1200px; height: 846px; overflow: hidden; background: var(--stage); }
  body { font-family: "Montserrat", sans-serif; position: relative; }

  .card {
    position: absolute; left: 280px; width: 640px; height: 356px;
    overflow: hidden; box-shadow: 0 8px 24px rgba(0,0,0,.45);
  }
  .card--front { top: 46px; background: var(--paper); color: var(--ink); }
  .card--back { top: 444px; background: var(--navy); color: var(--light); }

  /* Front */
  .name-tab { position: absolute; left: 0; top: 46px; width: 72px; height: 56px; background: var(--red); }
  .contact-strip { position: absolute; left: 0; top: 150px; width: 62px; height: 150px; background: var(--red); }
  .badge-icon { position: absolute; width: 26px; height: 26px; }
  .person-icon { left: 58px; top: 58px; }
  .holder { position: absolute; left: 96px; top: 54px; }
  .holder__name { font-weight: 700; font-size: 29px; letter-spacing: 1.5px; }
  .holder__role { font-size: 18px; letter-spacing: 1px; margin-top: 2px; }
  .holder__rule { position: absolute; left: 86px; top: 126px; width: 300px; height: 4px; background: var(--ink); }

  .contacts { position: absolute; left: 50px; top: 156px; list-style: none; }
  .contacts li { display: flex; align-items: center; height: 28px; font-size: 15px; letter-spacing: 1px; }
  .contacts svg { width: 22px; height: 22px; margin-right: 12px; flex: none; }

  .brand { position: absolute; font-weight: 700; color: var(--red); letter-spacing: 2px; text-transform: uppercase; }
  .card--front .brand { right: 34px; bottom: 22px; font-size: 20px; text-align: right; line-height: 1.2; }
  .card--back .brand { left: 352px; top: 56px; font-size: 22px; line-height: 1.2; }

  /* Back */
  .services { position: absolute; list-style: none; font-size: 15px; letter-spacing: 1px; line-height: 26px; }
  .services li::before {
    content: ""; display: inline-block; width: 8px; height: 8px; border-radius: 50%;
    background: var(--red); margin-right: 8px; vertical-align: 2px;
  }
  .services--left { left: 44px; top: 58px; }
  .services--right { left: 360px; top: 176px; }
  .divider { position: absolute; left: 318px; top: 146px; width: 4px; height: 72px; background: var(--light); }

  .appointment { position: absolute; display: flex; align-items: flex-end; font-size: 15px; letter-spacing: 1px; }
  .appointment::before {
    content: ""; width: 8px; height: 8px; border-radius: 50%; background: var(--red);
    margin-right: 8px; margin-bottom: 6px;
  }
  .appointment__line { width: 200px; height: 3px; background: var(--light); margin-left: 10px; margin-bottom: 4px; }
  .appointment--date { left: 44px; top: 170px; }
  .appointment--time { left: 360px; top: 290px; }
</style>
</head>
<body>

<section class="card card--front" aria-label="Business card front">
  <div class="name-tab"></div>
  <div class="contact-strip"></div>

  <svg class="badge-icon person-icon" viewBox="0 0 26 26" aria-hidden="true">
    <circle cx="13" cy="13" r="13" fill="#111"/>
    <circle cx="13" cy="8" r="3.2" fill="#fff"/>
    <path d="M8 20c0-4 2.2-7 5-7s5 3 5 7z" fill="#fff"/>
  </svg>

  <div class="holder">
    <p class="holder__name">Marlo Fenwicke</p>
    <p class="holder__role">(Managing director)</p>
  </div>
  <div class="holder__rule"></div>

  <ul class="contacts">
    <li>
      <svg viewBox="0 0 22 22" aria-hidden="true"><circle cx="11" cy="11" r="11" fill="#111"/><path d="M7.5 6l2 2.2-1.2 1.4a7 7 0 0 0 4 4l1.4-1.2 2.2 2-1.3 1.6C11 16 6 11 5.9 7.3z" fill="#fff"/></svg>
      027 451 9362
    </li>
    <li>
      <svg viewBox="0 0 22 22" aria-hidden="true"><circle cx="11" cy="11" r="11" fill="#111"/><rect x="6" y="9" width="10" height="7" rx="1" fill="#fff"/><path d="M5 9a6 3 0 0 1 12 0h-3v-1h-6v1z" fill="#fff"/></svg>
      07 594 2713
    </li>
    <li>
      <svg viewBox="0 0 22 22" aria-hidden="true"><circle cx="11" cy="11" r="11" fill="#111"/><rect x="5.5" y="7" width="11" height="8" rx="1" fill="#fff"/><path d="M5.5 7.5l5.5 4 5.5-4" stroke="#111" stroke-width="1.2" fill="none"/></svg>
      office@keelstoneautomotive.example.nz
    </li>
    <li>
      <svg viewBox="0 0 22 22" aria-hidden="true"><circle cx="11" cy="11" r="11" fill="#111"/><circle cx="11" cy="11" r="5.5" fill="none" stroke="#fff" stroke-width="1.3"/><path d="M5.5 11h11M11 5.5c-2.5 3-2.5 8 0 11M11 5.5c2.5 3 2.5 8 0 11" stroke="#fff" stroke-width="1.1" fill="none"/></svg>
      keelstoneautomotive.example.nz
    </li>
    <li>
      <svg viewBox="0 0 22 22" aria-hidden="true"><circle cx="11" cy="11" r="11" fill="#111"/><path d="M5 11l6-5 6 5h-1.8v5h-3v-3h-2.4v3h-3v-5z" fill="#fff"/></svg>
      48 Tarn Lane Marrowby 3580
    </li>
  </ul>

  <p class="brand">Keelstone Prime<br>Automotive</p>
</section>

<section class="card card--back" aria-label="Business card back">
  <ul class="services services--left">
    <li>Vehicle Servicing</li>
    <li>All Mechanical Repairs</li>
    <li>Warrant of Fitness</li>
  </ul>

  <p class="appointment appointment--date">Date<span class="appointment__line"></span></p>

  <p class="brand">Keelstone Prime<br>Automotive</p>

  <div class="divider"></div>

  <ul class="services services--right">
    <li>Tyres &amp; Wheel Alignments</li>
    <li>Automotive Parts &amp; Supplies</li>
    <li>Automotive Diagnostics</li>
  </ul>

  <p class="appointment appointment--time">Time<span class="appointment__line"></span></p>
</section>

</body>
</html>
```